Medical Marihuana Ziplock Bag Mockup Design

We seek skilled and professional designer for medical marihuana ziplock bag packaging design. We need a modern, minimal, clean Design with the name productname: Plomu - Endproduct will be a ziplock bag (see attachment) samples.
Product may but must not contain a cannabis leaf in Design7Logo

Target Market(s)

young audience

Industry/Entity Type

Medical

Logo Text

P L O M U

Font styles to use
Serif
Sans Serif

Colors
9bcb3c
abd037
cadf82
ffc214
fece3e
fee18a
6b449b
886aae
b8a6cd

Requirements
Nice to have
• Can but must not contain a minimal cannabis leaf as abstract sign

```html
<!DOCTYPE html>
<html lang="de">
<head>
<meta charset="utf-8">
<title>Plomu – Medical Marijuana 10g</title>
<link rel="stylesheet" href="https://fonts.googleapis.com/css2?family=Cormorant+Garamond:wght@500&family=Fira+Sans:wght@300;400;600&family=Josefin+Slab:wght@400&display=swap">
<style>
  :root {
    --green-top: #67983f;
    --green-dark: #2b5124;
    --green-mid: #5e913e;
    --green-light: #8bc43f;
    --leaf-light: #b9dc6a;
    --brand-green: #5f9438;
    --sub-green: #8bc43f;
    --grey-dark: #6b6c6e;
    --grey-light: #a3a4a6;
    --silver: #d9dadb;
    --white: #ffffff;
  }
  * { margin: 0; padding: 0; box-sizing: border-box; }
  html, body { width: 901px; height: 1200px; overflow: hidden; background: var(--white); }
  .bag {
    position: relative; width: 901px; height: 1200px; overflow: hidden;
    background: var(--white); font-family: "Fira Sans", sans-serif;
  }
  .top-band { position: absolute; left: 0; top: 0; width: 100%; height: 52px; background: var(--green-top); }
  .leaf-art {
    position: absolute; left: 0; top: 0; width: 435px; height: 385px;
    background: radial-gradient(ellipse at 15% 10%, var(--leaf-light) 0%, rgba(185,220,106,0.55) 45%, rgba(255,255,255,0) 75%);
  }
  .age { position: absolute; right: 24px; top: 74px; font-size: 40px; font-weight: 400; color: var(--brand-green); }
  .brand {
    position: absolute; left: 140px; top: 222px; width: 625px;
    font-family: "Cormorant Garamond", serif; font-weight: 500; font-size: 176px;
    line-height: 1; color: var(--brand-green); letter-spacing: -2px; text-align: center;
  }
  .info-band {
    position: absolute; left: 0; top: 451px; width: 100%; height: 163px;
    background: var(--green-dark); text-align: center;
  }
  .label-pill {
    position: absolute; left: 191px; top: 423px; width: 519px; height: 68px;
    border-radius: 30px; background: var(--green-light);
    box-shadow: 0 4px 6px rgba(0,0,0,0.35);
    color: var(--white); font-family: "Josefin Slab", serif; font-weight: 700;
    font-size: 42px; line-height: 72px; text-align: center; z-index: 2;
  }
  .origin { position: absolute; top: 66px; width: 100%; font-family: "Josefin Slab", serif; font-size: 28px; color: var(--white); letter-spacing: 0.5px; }
  .composition { position: absolute; top: 110px; width: 100%; font-family: "Josefin Slab", serif; font-size: 30px; color: var(--sub-green); }
  .silver-line { position: absolute; left: 0; width: 100%; height: 6px; background: linear-gradient(to bottom, var(--silver), #f4f4f4, var(--silver)); }
  .warning {
    position: absolute; left: 0; top: 620px; width: 100%; height: 410px;
    background: linear-gradient(160deg, var(--grey-dark) 0%, #8b8c8e 50%, var(--grey-light) 100%);
    color: var(--white); text-align: center; font-weight: 600;
    font-size: 38px; line-height: 48px; padding-top: 22px;
  }
  .warning p { margin-bottom: 10px; text-shadow: 0 1px 3px rgba(0,0,0,0.35); }
  .bottom-band {
    position: absolute; left: 0; top: 1036px; width: 100%; height: 164px;
    background: linear-gradient(170deg, var(--green-mid) 0%, var(--green-dark) 100%);
  }
  .weight { position: absolute; left: 50px; top: 50px; font-size: 62px; font-weight: 400; color: var(--white); }
  .cross { position: absolute; left: 654px; top: 35px; }
  .type-list { position: absolute; left: 785px; top: 40px; list-style: none; }
  .type-list li {
    display: flex; align-items: center; height: 30px;
    font-family: "Cormorant Garamond", serif; font-size: 17px; color: var(--white); letter-spacing: 0.5px;
  }
  .type-list .box { width: 19px; height: 19px; background: var(--white); border: 2px solid #222; margin-right: 10px; }
</style>
</head>
<body>
<div class="bag">
  <div class="top-band"></div>
  <div class="leaf-art" role="img" aria-label="Large light green cannabis leaf illustration in the top left corner"></div>
  <div class="age">18+</div>
  <div class="brand">PLOMU</div>

  <div class="label-pill">Medical Marijuana</div>
  <div class="info-band">
    <div class="origin">100% SCHWEIZER HANF</div>
    <div class="composition">Product auf pflanzlicher Basis ohne Tabak</div>
  </div>

  <div class="silver-line" style="top:613px"></div>
  <div class="warning">
    <p>Rauchen fügt ihnen und den<br>Menschen in ihrer Umgebung<br>erheblichen Schaden zu.</p>
    <p>Fumer nuit Gravement à votre<br>santé et à celle de votre entourage.</p>
    <p>Il fumo daneggia gravemente<br>te e chi ti sta intorno.</p>
  </div>
  <div class="silver-line" style="top:1029px"></div>

  <div class="bottom-band">
    <div class="weight">10g</div>
    <svg class="cross" width="96" height="96" viewBox="0 0 96 96" aria-hidden="true">
      <path d="M30 0h36v30h30v36H66v30H30V66H0V30h30z" fill="#66a33f"/>
    </svg>
    <ul class="type-list">
      <li><span class="box"></span>INDICA</li>
      <li><span class="box"></span>SATIVA</li>
      <li><span class="box"></span>HYBRID</li>
    </ul>
  </div>
</div>
</body>
</html>
```